Business Card Design For Marketing Agnecy LVP

Need business card design for marketing agency.

Doug Fenwick
President, CEO
1-555-302-4196
doug@boldpromoperksgroup.example
www.BoldPromoPerksGroup.example

Back Side:
Boost Sales Using Rewards, Incentives & Giveaways
Get A Free Sample Package

Target Market(s)

B2B

Industry/Entity Type

Marketing

Contact Information for Business Card

Doug Fenwick
President, CEO
1-555-302-4196

Back Side:
Get A Free Sample Package

Please note that my current url is OLD DESIGN. I am working on new design and want the business card to match color themes at least on new site. Here is the demo link for new site so you can see the colors I use, etc.

http://layoutcratehub.example/kq/doug/lvp_final/index.html

Requirements
Must have
• Please note that my current url is OLD DESIGN. I am working on new design and want the business card to match color themes at least on new site. Here is the demo link for new site so you can see the colors I use, etc.

Nice to have

Should not have

```html
<!DOCTYPE html>
<html lang="en">
<head>
<meta charset="utf-8">
<title>LVP Business Card</title>
<link rel="stylesheet" href="https://fonts.googleapis.com/css2?family=Exo+2:wght@600;700;800&family=Roboto:wght@400;500&family=Roboto+Condensed:wght@400&display=swap">
<style>
  :root {
    --backdrop: #b3b3b3;
    --card: #f1f1f1;
    --card-edge: #e4e4e4;
    --brand-blue: #2a5aa0;
    --charcoal: #3d3d3f;
    --text-grey: #4a4a4a;
    --promo-green: #4fae3a;
    --promo-green-dark: #3f9a2c;
    --white: #ffffff;
  }
  * { margin: 0; padding: 0; box-sizing: border-box; }
  html, body { width: 1200px; height: 576px; overflow: hidden; }
  body {
    background: var(--backdrop);
    position: relative;
    font-family: "Roboto", Arial, sans-serif;
  }
  .card {
    position: absolute;
    background: linear-gradient(180deg, var(--white) 0%, var(--card) 60%, var(--card-edge) 100%);
    border-radius: 10px;
    overflow: hidden;
  }
  .card--front { left: 82px; top: 139px; width: 484px; height: 293px; }
  .card--back  { left: 602px; top: 138px; width: 480px; height: 291px; }

  .brand {
    position: absolute;
    display: flex;
    align-items: center;
    gap: 10px;
    color: var(--brand-blue);
    font-family: "Exo 2", Arial, sans-serif;
    font-weight: 700;
    letter-spacing: 0.5px;
    white-space: nowrap;
  }
  .brand__dot { width: 14px; height: 14px; border-radius: 50%; background: var(--brand-blue); flex: none; }
  .card--front .brand { left: 0; right: 0; top: 48px; justify-content: center; font-size: 26px; }
  .card--back .brand { left: 26px; top: 46px; font-size: 25px; }

  .offer-banner { position: absolute; left: 64px; top: 147px; width: 356px; height: 62px; }
  .offer-banner svg { position: absolute; inset: 0; }
  .offer-banner__line {
    position: absolute; left: 0; right: 0; text-align: center; color: var(--white);
  }
  .offer-banner__tagline { top: 10px; font-size: 12.5px; }
  .offer-banner__cta {
    top: 26px; font-family: "Exo 2", Arial, sans-serif; font-weight: 800;
    font-size: 14px; letter-spacing: 0.6px;
  }

  .site-link {
    position: absolute; left: 0; right: 0; top: 238px; text-align: center;
    font-size: 13px; color: var(--text-grey);
  }
  .site-link__name { color: var(--brand-blue); }

  .base-band { position: absolute; left: 0; right: 0; bottom: 0; height: 11px; display: flex; }
  .base-band__blue { width: 50%; background: var(--brand-blue); }
  .base-band__dark { flex: 1; background: var(--charcoal); }

  .person { position: absolute; left: 26px; top: 177px; }
  .person__name {
    font-family: "Exo 2", Arial, sans-serif; font-weight: 700;
    font-size: 19px; color: var(--brand-blue);
  }
  .person__title { font-size: 11.5px; color: var(--text-grey); margin-top: 2px; }

  .contact-list { position: absolute; left: 226px; top: 180px; list-style: none; }
  .contact-list li {
    display: flex; align-items: center; gap: 8px; height: 18px;
    font-family: "Roboto Condensed", Arial, sans-serif; font-size: 12.5px; color: var(--text-grey);
  }
  .contact-list svg { width: 11px; height: 11px; fill: var(--charcoal); flex: none; }

  .back-footer { position: absolute; left: 0; right: 0; bottom: 0; height: 36px; }
  .back-footer svg { position: absolute; inset: 0; }
  .back-footer__cta {
    position: absolute; left: 190px; right: 0; top: 12px; text-align: center; color: var(--white);
    font-family: "Exo 2", Arial, sans-serif; font-weight: 800; font-size: 13.5px; letter-spacing: 0.5px;
  }
</style>
</head>
<body>

<section class="card card--front" aria-label="Card front">
  <div class="brand"><span class="brand__dot"></span>BOLD PROMO PERKS GROUP</div>

  <div class="offer-banner">
    <svg viewBox="0 0 356 62" width="356" height="62" aria-hidden="true">
      <polygon points="6,50 178,57 350,50 350,54 178,61 6,54" fill="var(--charcoal)"/>
      <polygon points="0,0 356,0 350,42 178,50 6,42" fill="var(--promo-green)"/>
      <polygon points="6,42 178,50 350,42 349,46 178,53 7,46" fill="var(--promo-green-dark)"/>
    </svg>
    <div class="offer-banner__line offer-banner__tagline">Boost Sales Using Rewards, Incentives &amp; Giveaways</div>
    <div class="offer-banner__line offer-banner__cta">GET A FREE SAMPLE PACKAGE</div>
  </div>

  <p class="site-link">www.<span class="site-link__name">BoldPromoPerksGroup</span>.example</p>

  <div class="base-band"><span class="base-band__blue"></span><span class="base-band__dark"></span></div>
</section>

<section class="card card--back" aria-label="Card back">
  <div class="brand"><span class="brand__dot"></span>BOLD PROMO PERKS GROUP</div>

  <div class="person">
    <p class="person__name">Doug Fenwick</p>
    <p class="person__title">President, CEO</p>
  </div>

  <ul class="contact-list">
    <li>
      <svg viewBox="0 0 12 12" aria-hidden="true"><path d="M1 4c0-2 2-3 5-3s5 1 5 3l-3 .5-.5-1.5h-3L4 4.5zM3 5h6l1.5 6h-9z"/></svg>
      1-555-302-4196
    </li>
    <li>
      <svg viewBox="0 0 12 12" aria-hidden="true"><path d="M0 2h12v8H0zM1 3l5 4 5-4v-.2H1z" fill-rule="evenodd"/></svg>
      doug@boldpromoperksgroup.example
    </li>
    <li>
      <svg viewBox="0 0 12 12" aria-hidden="true"><path d="M6 0a6 6 0 1 0 0 12A6 6 0 0 0 6 0zm0 1c.8 0 1.6 1.7 1.8 4.5H4.2C4.4 2.7 5.2 1 6 1zM1 6.5h2.2c.1 1.6.4 3 .9 3.9A5 5 0 0 1 1 6.5zm0-1a5 5 0 0 1 3.1-3.9c-.5.9-.8 2.3-.9 3.9zm3.2 1h3.6C7.6 9.3 6.8 11 6 11s-1.6-1.7-1.8-4.5zm4.6 0H11a5 5 0 0 1-3.1 3.9c.5-.9.8-2.3.9-3.9zm0-1c-.1-1.6-.4-3-.9-3.9A5 5 0 0 1 11 5.5z"/></svg>
      www.BoldPromoPerksGroup.example
    </li>
  </ul>

  <div class="back-footer">
    <svg viewBox="0 0 480 36" width="480" height="36" preserveAspectRatio="none" aria-hidden="true">
      <rect x="0" y="25" width="480" height="11" fill="var(--charcoal)"/>
      <path d="M190 36 L200 8 Q203 0 212 0 H480 V36 Z" fill="var(--brand-blue)"/>
    </svg>
    <div class="back-footer__cta">GET A FREE SAMPLE PACKAGE</div>
  </div>
</section>

</body>
</html>
```